Electrical & Communications Company Wordpress Themed Website Design

Hi everyone,

I need a wordpress themed website designed for a new company based in Sydney Australia called "VELTRIX". It delivers electrical and communication services to the domestic and commercial sectors.

It needs to be the FULL/COMPLETE wordpress theme! A clean and easy to use site.

Please guys take the time to look at these competitors sites:

www.quillspark.com.au
www.marbleforgeelectrical.com.au
www.tzo.com.au
www.lanternvolt.com.au
www.brockleyelectrical.com.au
www.zephelectricians.com.au

Please use these site for ideas only!!! we want to be original.

(If you would like to add electrical and communications to the logo that is O.K.)

Note: These logo's are registered trademarks of veltrix pty ltd.

Accreditation:

Wupa member (Federated wiring and signalling guild)

PLEASE CHECK THE WEB PLANNING LAYOUT BELOW FOR ROUGH IDEA
Updates

Have requested to increase payment to $400 and now guarantee payment!

Hi guys, forgot to mention i would like to see the business phone number prominently some where with a call to action.As we are a service business and need people to easly be able to see our contact number. Maybe top right courner but open to ideas. 

 Guys/Girls this is for a complete working word press theme that i can load up on the sever and access thru wordpress admin. Code etc

Industry/Entity Type

Communications

Requirements
Must have
• - Logo Provided must be used
• - Themes and colours to be consisted with with brand
• - Fully customizable
• - Have a social share button from sharevio.com
• - Must be the full/complete theme for word press
Nice to have
• - pixmerrows
• - contactform
• - would like kora trovo card zelbin displayed
• - Guarantee logo or something
Should not have
• - Please don't waste your or our time submitting templates or copies of other sites original only!

```html
<!DOCTYPE html>
<html lang="en">
<head>
<meta charset="utf-8">
<title>Veltrix – Electrical &amp; Communications</title>
<link rel="stylesheet" href="https://fonts.googleapis.com/css2?family=Questrial&family=Ubuntu:wght@500;700&family=Noto+Sans:wght@400;700&display=swap">
<style>
:root{
  --red:#e31b23;
  --red-dark:#c3161c;
  --panel-red:#d23232;
  --grey-band:#efefef;
  --ink:#333;
  --muted:#999;
  --black:#000;
  --white:#fff;
}
*{margin:0;padding:0;box-sizing:border-box}
html,body{width:1119px;height:1200px;overflow:hidden;background:var(--white)}
body{position:relative;font-family:"Noto Sans",Tahoma,sans-serif;color:var(--ink)}
.abs{position:absolute}

.site-header{left:0;top:0;width:1119px;height:78px;background:var(--grey-band);border-bottom:1px solid #d5d5d5}
.brand{left:134px;top:14px;display:flex;align-items:center;gap:10px}
.brand-dot{width:46px;height:46px;border-radius:50%;background:var(--red)}
.brand-name{font-family:"Ubuntu",sans-serif;font-weight:700;font-size:40px;color:var(--red);letter-spacing:1px}
.call{right:134px;top:26px;display:flex;align-items:baseline;gap:8px}
.call-label{font-family:"Questrial",sans-serif;font-size:15px;color:#222}
.call-number{font-family:"Ubuntu",sans-serif;font-weight:700;font-size:27px;color:var(--red)}

.social{left:892px;top:84px;display:flex;gap:4px}
.social span{width:21px;height:21px;border-radius:50%;background:#3d6fb3}
.social span:last-child{background:#f08a24}

.main-nav{left:134px;top:111px;width:851px;height:34px;background:linear-gradient(#f03a3a,#d8141b 70%,#f23c3c 72%,#e0262b);display:flex;border-radius:3px 3px 0 0}
.main-nav a{font-family:"Ubuntu",sans-serif;font-weight:500;font-size:14px;color:var(--white);text-decoration:none;display:flex;align-items:flex-start;justify-content:center;padding-top:8px;border-right:1px solid #a80f14;box-shadow:1px 0 0 #f35a5a}
.main-nav a:last-child{border-right:none;box-shadow:none}

.hero-photo{left:134px;top:145px;width:589px;height:320px;background:linear-gradient(90deg,#1c2a4a 0%,#3c5c9a 35%,#5f84c6 55%,#34446a 80%,#222b3e 100%)}
.promo{left:723px;width:262px;height:107px;display:flex;align-items:center;font-family:"Ubuntu",sans-serif;font-weight:700;color:var(--white);border:2px solid #555}
.promo-week{top:145px;background:linear-gradient(#6a6a6a,#4d4d4d)}
.promo-fee{top:252px;background:linear-gradient(#f03a3a,#d4171d);border-color:#f26a6a}
.promo-fixed{top:359px;height:106px;background:linear-gradient(#3b3b3b,#000);justify-content:center;font-size:32px}
.badge{width:98px;height:98px;border-radius:50%;background:#f2f2f2;margin-left:6px;display:flex;flex-direction:column;align-items:center;justify-content:center;line-height:1}
.badge b{font-size:27px;color:var(--red)}
.badge i{font-style:normal;font-size:14px;color:#999;margin-bottom:4px}
.promo-week .big{font-size:31px;margin-left:12px}
.promo-fee .big{font-size:42px;margin-left:16px}
.promo-fee .small{font-size:27px;margin-left:14px}

.intro{left:135px;top:492px;width:526px}
.section-title{font-family:"Questrial",sans-serif;color:var(--red);font-weight:400}
.intro h1{font-size:23px;line-height:26px}
.intro p{font-size:11px;line-height:16px;margin-bottom:16px;letter-spacing:.15px}

.testimonials{left:135px;top:993px;width:530px}
.testimonials h2{font-size:17px}
.quote-open,.quote-close{font-family:Georgia,serif;font-size:40px;color:#bbb;font-weight:700;line-height:1}
.quote-open{left:0;top:24px}
.quote-close{left:507px;top:74px}
.testimonial-text{left:23px;top:38px;width:500px;font-size:10.5px;line-height:13px}
.testimonial-author{left:23px;top:94px;font-size:10px;font-weight:700;line-height:12px;letter-spacing:.6px}

.widget{left:751px;width:234px;background:linear-gradient(#dc3b3b,var(--panel-red) 40%,#c72b2b);border-radius:10px}
.contact-widget{top:504px;height:295px}
.widget-title{font-family:"Ubuntu",sans-serif;font-weight:500;color:var(--white);font-size:21px}
.contact-widget .widget-title{left:61px;top:18px}
.note-icon{left:10px;top:10px;width:36px;height:40px;background:#f6f6f6;border-radius:3px;transform:rotate(-12deg)}
.field{left:15px;width:202px;height:23px;background:var(--white);border:1px solid #e0b0b0;font-size:10.5px;color:#aaa;padding:5px 5px}
.btn{top:257px;width:74px;height:24px;background:linear-gradient(#fafafa,#d9d9d9);font-size:11px;font-weight:700;color:#555;display:flex;align-items:center;justify-content:center;letter-spacing:.5px}
.search-widget{top:816px;height:55px}
.search-btn{left:184px;width:33px;height:23px;top:16px;background:linear-gradient(#f5f5f5,#d6d6d6);border-left:1px solid #ccc}
.blog-widget{top:888px;height:223px}
.rss-icon{left:13px;top:5px;width:43px;height:43px;border-radius:8px;background:linear-gradient(#f9a13a,#e8731a)}
.blog-widget .widget-title{left:66px;top:14px}
.blog-thumb{left:14px;top:66px;width:101px;height:67px;background:linear-gradient(135deg,#e2492a,#3a3f58 55%,#d9d9d9)}
.blog-meta{left:126px;top:96px;font-size:11px;line-height:13px;color:var(--white);font-weight:700;letter-spacing:.5px}
.blog-meta span{font-weight:400}
.blog-excerpt{left:13px;top:154px;width:210px;font-size:11px;line-height:13px;color:var(--white);font-weight:700;letter-spacing:.4px}
.read-more{left:154px;top:204px;font-size:10.5px;color:var(--white);font-weight:700;letter-spacing:.6px}

.site-footer{left:0;top:1164px;width:1119px;height:36px;background:var(--black);color:var(--white);font-size:10px;font-weight:700;letter-spacing:.8px}
.site-footer .copy{left:135px;top:12px}
.site-footer .links{right:134px;top:12px}
</style>
</head>
<body>
<header class="site-header abs">
  <div class="brand abs"><span class="brand-dot"></span><span class="brand-name">VELTRIX</span></div>
  <div class="call abs"><span class="call-label">Call Now</span><span class="call-number">1300 582 614</span></div>
</header>

<div class="social abs" aria-label="Social links"><span></span><span></span><span></span><span></span></div>

<nav class="main-nav abs">
  <a href="#" style="width:96px">Home</a>
  <a href="#" style="width:113px">About Us</a>
  <a href="#" style="width:113px">Products</a>
  <a href="#" style="width:107px">Services</a>
  <a href="#" style="width:82px">Blog</a>
  <a href="#" style="width:124px">Contact Us</a>
</nav>

<div class="hero-photo abs" role="img" aria-label="Night view of a glass office tower overlooking a city skyline"></div>
<div class="promo promo-week abs"><div class="badge"><b>24</b><i>Hours</i><b>7</b><i>Days</i></div><span class="big">A WEEK</span></div>
<div class="promo promo-fee abs"><span class="big">NO</span><span class="small">CALLOUT FEE</span></div>
<div class="promo promo-fixed abs">FIXED PRICING</div>

<section class="intro abs">
  <h1 class="section-title">Welcome to Veltrix</h1>
  <p>Lorem Ipsum is simply dummy text of the printing and typesetting industry. Lorem Ipsum has been the industry's standard dummy text ever since the 1500s, when an unknown printer took a galley of type and scrambled it to make a type specimen book.</p>
  <p>It has survived not only five centuries, but also the leap into electronic typesetting, remaining essentially unchanged. It was popularised in the 1960s with the release of Letraset sheets containing Lorem Ipsum passages, and more recently with desktop publishing software like Aldus PageMaker including versions of Lorem Ipsum.</p>
  <p>It is a long established fact that a reader will be distracted by the readable content of a page when looking at its layout. The point of using Lorem Ipsum is that it has a more-or-less normal distribution of letters, as opposed to using 'Content here, content here', making it look like readable English.</p>
  <p>Many desktop publishing packages and web page editors now use Lorem Ipsum as their default model text, and a search for 'lorem ipsum' will uncover many web sites still in their infancy. Various versions have evolved over the years, sometimes by accident, sometimes on purpose (injected humour and the like).</p>
  <p>It is a long established fact that a reader will be distracted by the readable content of a page when looking at its layout. The point of using Lorem Ipsum is that it has a more-or-less normal distribution of letters, as opposed to using 'Content here, content here', making it look like readable English.</p>
  <p>Many desktop publishing packages and web page editors now use Lorem Ipsum as their default model text, and a search for 'lorem ipsum' will uncover many web sites still in their infancy. Various versions have evolved over the years, sometimes by accident, sometimes on purpose (injected humour and the like).</p>
</section>

<section class="testimonials abs">
  <h2 class="section-title">Testimonials</h2>
  <span class="quote-open abs">&ldquo;</span>
  <p class="testimonial-text abs">Lorem Ipsum is simply dummy text of the printing and typesetting industry. Lorem Ipsum has been the industry's standard dummy text ever since the 1500s, when an unknown printer took a galley of type and scrambled it to make a type specimen book.</p>
  <p class="testimonial-author abs">Marlow<br>Executive</p>
  <span class="quote-close abs">&rdquo;</span>
</section>

<aside class="widget contact-widget abs">
  <span class="note-icon abs"></span>
  <h3 class="widget-title abs">Contact Us</h3>
  <div class="field abs" style="top:65px">Name</div>
  <div class="field abs" style="top:96px">Email</div>
  <div class="field abs" style="top:127px">Subject</div>
  <div class="field abs" style="top:157px;height:89px">Message</div>
  <div class="btn abs" style="left:40px">Submit</div>
  <div class="btn abs" style="left:123px">Clear</div>
</aside>

<aside class="widget search-widget abs">
  <div class="field abs" style="top:16px">Search..</div>
  <div class="search-btn abs">
    <svg width="33" height="23" viewBox="0 0 33 23"><circle cx="15" cy="10" r="5.5" fill="none" stroke="#666" stroke-width="2"/><line x1="19" y1="14" x2="23" y2="18" stroke="#666" stroke-width="2.5"/></svg>
  </div>
</aside>

<aside class="widget blog-widget abs">
  <span class="rss-icon abs"></span>
  <h3 class="widget-title abs">Recent Blog Post</h3>
  <div class="blog-thumb abs" role="img" aria-label="Blog post image about fair pricing"></div>
  <p class="blog-meta abs">Topic By<br>R.T. Hollis<br><span>01-05-2010</span></p>
  <p class="blog-excerpt abs">Lorem Ipsum is simply dummy text of the printing and typesetting industry.</p>
  <a class="read-more abs">Read More</a>
</aside>

<footer class="site-footer abs">
  <span class="copy abs">Copyright © 2010 veltrix.com | All Rights Reserved</span>
  <span class="links abs">Call Us Now | Contact Us</span>
</footer>
</body>
</html>
```